Business Card Design for a Software Startup

We'd like to have a business card design. We already have a logo. Basically what we need is a clean design with name, address, cellphone and phone numbers, e-mail and web site address (front) and a space on the back with our logo with the company name on the right side and some texts on the bottom.
We are a development and consulting company in Brazil with highly qualified team of professionals in Java, iOS and Android development and consulting.

Target Market(s)

CIO, IT managers of mid to big size companies

Industry/Entity Type

Business

```html
<!DOCTYPE html>
<html lang="en">
<head>
<meta charset="utf-8">
<title>Keldris Business Card</title>
<link href="https://fonts.googleapis.com/css2?family=Montserrat:wght@400;600;700&display=swap" rel="stylesheet">
<style>
  :root {
    --backdrop: #e8e8e6;
    --card: #ffffff;
    --navy: #0f3a63;
    --blue: #1d6ea6;
    --mark: #1a6aa3;
    --ink: #4f5256;
    --shadow: rgba(0, 0, 0, 0.18);
  }
  * { margin: 0; padding: 0; box-sizing: border-box; }
  html, body { width: 1200px; height: 720px; overflow: hidden; }
  body {
    background: var(--backdrop);
    font-family: "Montserrat", sans-serif;
    position: relative;
  }
  .card {
    position: absolute;
    width: 540px;
    height: 309px;
    background: var(--card);
    box-shadow: 0 6px 18px var(--shadow);
  }
  .card--contact { left: 40px; top: 70px; }
  .card--brand { left: 620px; top: 340px; }

  .wordmark {
    font-family: "Montserrat", sans-serif;
    font-weight: 700;
    color: var(--navy);
    letter-spacing: 1px;
    line-height: 1;
    white-space: nowrap;
  }
  .card--contact .wordmark {
    position: absolute;
    left: 42px;
    top: 54px;
    font-size: 42px;
  }
  .brand-square {
    position: absolute;
    background: var(--mark);
    border-radius: 12px;
  }
  .card--contact .brand-square {
    right: 50px;
    top: 40px;
    width: 130px;
    height: 130px;
  }

  .person {
    position: absolute;
    left: 42px;
    top: 124px;
  }
  .person__name {
    font-size: 18px;
    font-weight: 700;
    color: var(--blue);
  }
  .person__title {
    font-size: 13px;
    font-weight: 400;
    color: var(--ink);
  }
  .address {
    position: absolute;
    left: 42px;
    top: 156px;
    font-size: 11.5px;
    line-height: 1.3;
    color: var(--ink);
  }
  .contacts {
    position: absolute;
    left: 42px;
    top: 198px;
    list-style: none;
    font-size: 12.5px;
    line-height: 1.55;
    color: var(--ink);
  }
  .contacts__label {
    display: inline-block;
    width: 20px;
    color: var(--blue);
  }

  .lockup {
    position: absolute;
    left: 0;
    right: 0;
    top: 108px;
    display: flex;
    justify-content: center;
    align-items: center;
    gap: 16px;
  }
  .card--brand .brand-square {
    position: static;
    width: 72px;
    height: 72px;
    border-radius: 8px;
    flex: none;
  }
  .card--brand .wordmark { font-size: 58px; }
  .web {
    position: absolute;
    right: 90px;
    bottom: 66px;
    font-size: 14px;
    font-weight: 600;
    letter-spacing: 5px;
    color: var(--ink);
  }
  .web__domain { color: var(--blue); }
</style>
</head>
<body>
  <section class="card card--contact">
    <div class="wordmark">KELDRIS</div>
    <div class="brand-square"></div>
    <p class="person">
      <span class="person__name">Your Name,</span>
      <span class="person__title">Title</span>
    </p>
    <p class="address">Door No. Street Name<br>City Name, State, Zip Code</p>
    <ul class="contacts">
      <li><span class="contacts__label">P:</span>123-456-7890</li>
      <li><span class="contacts__label">C:</span>123-456-7890</li>
      <li><span class="contacts__label">E:</span>yourname@keldris.com</li>
      <li><span class="contacts__label">W:</span>www.keldris.com</li>
    </ul>
  </section>

  <section class="card card--brand">
    <div class="lockup">
      <div class="brand-square"></div>
      <div class="wordmark">KELDRIS</div>
    </div>
    <p class="web">www.<span class="web__domain">keldris</span>.com</p>
  </section>
</body>
</html>
```